Business Card Design Project

Business card based on attached logo

Todd Merrick
Todd@lorvantest.com
877-514-9073 ext. 318
Www.LorvanTest.com

Industry/Entity Type

Business

```html
<!DOCTYPE html>
<html lang="en">
<head>
<meta charset="utf-8">
<title>LorvanTest Business Cards</title>
<link rel="stylesheet" href="https://fonts.googleapis.com/css2?family=Roboto:wght@400;900&display=swap">
<style>
  :root {
    --backdrop: #8a8c8f;
    --ink: #1f1d1e;
    --red: #e3222b;
    --red-deep: #b8202a;
    --white: #ffffff;
    --paper-light: #ffffff;
    --paper-shade: #dcdcdc;
    --charcoal: #3a3a3a;
    --charcoal-deep: #161616;
  }
  * { margin: 0; padding: 0; box-sizing: border-box; }
  html, body { width: 1200px; height: 720px; overflow: hidden; }
  body {
    background: var(--backdrop);
    font-family: "Roboto", Arial, sans-serif;
    position: relative;
  }
  .card {
    position: absolute;
    width: 565px;
    height: 322px;
    border-radius: 20px;
    overflow: hidden;
  }
  .card--contact { left: 24px; top: 27px; background: linear-gradient(180deg, var(--paper-light), var(--paper-shade)); }
  .card--white { left: 609px; top: 27px; background: var(--white); border: 1px solid #555; }
  .card--dark { left: 24px; top: 372px; background: radial-gradient(ellipse at 50% 30%, var(--charcoal), var(--charcoal-deep) 80%); }
  .card--red { left: 609px; top: 372px; background: linear-gradient(135deg, var(--red), var(--red-deep)); }

  .brand {
    position: absolute;
    display: flex;
    align-items: center;
    gap: 10px;
    font-weight: 900;
    letter-spacing: -1px;
    white-space: nowrap;
  }
  .brand__mark { display: inline-block; background: var(--red); }
  .brand--dark { color: var(--ink); }
  .brand--light { color: var(--white); }

  .card--contact .brand { left: 34px; top: 92px; font-size: 42px; }
  .card--contact .brand__mark { width: 18px; height: 18px; }
  .card--white .brand, .card--dark .brand { left: 0; right: 0; justify-content: center; top: 112px; font-size: 72px; }
  .brand__mark--lg { width: 30px; height: 30px; }
  .card--red .brand { left: 34px; top: 40px; font-size: 72px; }

  .divider { position: absolute; left: 298px; top: 55px; width: 1px; height: 140px; background: #bdbdbd; }
  .contact { position: absolute; left: 318px; top: 88px; color: var(--ink); }
  .contact__name { color: var(--red); font-size: 19px; letter-spacing: 0.3px; margin-bottom: 22px; }
  .contact__line { display: flex; align-items: center; gap: 7px; font-size: 17px; margin-bottom: 8px; }
  .contact__line svg { width: 13px; height: 13px; fill: var(--red); }

  .swoosh { position: absolute; left: 0; top: 0; width: 565px; height: 322px; }

  .website {
    position: absolute;
    font-size: 17px;
    letter-spacing: 2.6px;
  }
  .card--contact .website { left: 0; right: 0; text-align: center; top: 295px; color: var(--white); }
  .card--white .website { left: 0; right: 0; text-align: center; top: 278px; color: var(--ink); }
  .card--dark .website { left: 0; right: 0; text-align: center; top: 290px; color: var(--white); }
  .card--red .website { left: 34px; top: 300px; color: var(--white); }

  .faint-square {
    position: absolute;
    left: 440px; top: 160px;
    width: 150px; height: 150px;
    background: rgba(255,255,255,0.12);
  }
</style>
</head>
<body>

<section class="card card--contact">
  <svg class="swoosh" viewBox="0 0 565 322" aria-hidden="true">
    <path d="M0 250 C150 300 360 305 565 268 L565 322 L0 322 Z" fill="var(--red-deep)"/>
    <path d="M0 255 C150 302 360 306 565 272 L565 286 C360 318 150 312 0 270 Z" fill="var(--red)"/>
    <path d="M0 218 C140 275 330 298 490 292 C330 290 150 268 0 236 Z" fill="var(--ink)"/>
  </svg>
  <div class="brand brand--dark"><span>LorvanTest</span><span class="brand__mark"></span></div>
  <div class="divider"></div>
  <div class="contact">
    <p class="contact__name">TODD MERRICK</p>
    <p class="contact__line">
      <svg viewBox="0 0 16 16" aria-hidden="true"><path d="M3 1h3l1 4-2 1a9 9 0 0 0 5 5l1-2 4 1v3c0 1-1 2-2 2A13 13 0 0 1 1 3c0-1 1-2 2-2z"/></svg>
      877-514-9073 ext. 318
    </p>
    <p class="contact__line">
      <svg viewBox="0 0 16 16" aria-hidden="true"><path d="M1 4h14v9H1z M1 4l7 5 7-5" stroke="#fff" stroke-width="1"/></svg>
      Todd@lorvantest.com
    </p>
  </div>
  <p class="website">www.lorvantest.com</p>
</section>

<section class="card card--white">
  <div class="brand brand--dark"><span>LorvanTest</span><span class="brand__mark brand__mark--lg"></span></div>
  <p class="website">www.lorvantest.com</p>
</section>

<section class="card card--dark">
  <div class="brand brand--light"><span>LorvanTest</span><span class="brand__mark brand__mark--lg"></span></div>
  <p class="website">www.lorvantest.com</p>
</section>

<section class="card card--red">
  <div class="faint-square"></div>
  <div class="brand brand--light"><span>LorvanTest</span></div>
  <p class="website">www.lorvantest.com</p>
</section>

</body>
</html>
```